Harrow Tavern & Grille Menu Makeover

I am looking for a professional look to update our current menu. We are an independently owned sports bar and grill. Up to this point, I have done all of my own graphic designing. I am looking for something classy/family oriented. We are a very family friendly sports bar that offers a wide variety of menu options. Our website is www.harrowtavernco.example. This may help you get more of a feel for what type of place we are and what we offer. Our menu is listed on the website. My current menu is 8.5x14 inserts that feature a cover page, 4 inside pages and a back page. I would like something a little more condensed than this. Possibly a large tri-fold menu? I am open to all new ideas. I do have some pictures on my menu now, and would like to continue using a few pictures to feature some of my items. I would like something that is in a format that gives me the option to change items and prices on my own in the future. I would also like it to feature, or inform my patrons about our technology that we offer. We offer online ordering and we are a "verified venue" with Brewvoke.( a social site for craft beer lovers).

Industry/Entity Type

Sports Bar

Requirements
Nice to have
• Nice to have some pictures, but does not have to. We do feature 9 different beers on tap. A lot of them are local craft beers from the state of Kansas. Not sure if that is something we can feature, but it is a nice talking point. All of our tables and bar are hand built. With a rich mahogany finish on all of our woodwork, some type of "woodgrain" look into the menu would be nice.

```html
<!DOCTYPE html>
<html lang="en">
<head>
<meta charset="utf-8">
<title>Harrow Tavern &amp; Grille — Entrees &amp; Sandwiches</title>
<link rel="stylesheet" href="https://fonts.googleapis.com/css2?family=Playfair+Display:wght@700&family=Oswald:wght@300;400&family=Montserrat:wght@700&display=swap">
<style>
  :root {
    --page: #141617;
    --panel: #0b0d0e;
    --gold: #e2c07a;
    --gold-deep: #c79a4c;
    --gold-light: #f3dca2;
    --body-text: #d8c79f;
  }
  * { margin: 0; padding: 0; box-sizing: border-box; }
  html, body { width: 850px; height: 1200px; overflow: hidden; background: var(--page); }
  .menu-page { position: relative; width: 850px; height: 1200px; background: var(--page); }

  .hero-photo {
    position: absolute; left: 0; top: 0; width: 850px; height: 380px;
    background:
      radial-gradient(ellipse 190px 80px at 250px 95px, #c89a3e 0%, #9a7430 55%, transparent 100%),
      radial-gradient(ellipse 200px 90px at 620px 55px, #cfc6b0 0%, #8a8577 60%, transparent 100%),
      radial-gradient(ellipse 520px 220px at 420px 170px, #6a3a22 0%, #3a2218 60%, transparent 100%),
      linear-gradient(180deg, #2b1d16 0%, #3c271c 40%, var(--page) 100%);
  }

  .menu-panel {
    position: absolute; left: 68px; top: 218px; width: 712px; height: 916px;
    background: var(--panel); border-radius: 10px;
  }

  .section-title {
    position: absolute; left: 26px;
    font-family: "Playfair Display", serif; font-weight: 700;
    font-size: 37px; letter-spacing: 0.5px; line-height: 1;
    color: var(--gold);
    background: linear-gradient(180deg, var(--gold-light), var(--gold-deep));
    -webkit-background-clip: text; background-clip: text; -webkit-text-fill-color: transparent;
  }
  .section-title.entrees { top: 26px; }
  .section-title.sandwiches { top: 460px; }

  .item-column {
    position: absolute; width: 312px;
    display: flex; flex-direction: column; gap: 6px;
  }
  .col-left { left: 30px; }
  .col-right { left: 359px; width: 330px; }
  .entrees-list { top: 70px; }
  .sandwiches-list { top: 504px; }

  .item-name {
    font-family: "Oswald", sans-serif; font-weight: 400;
    font-size: 16px; line-height: 18px; color: var(--gold);
    text-transform: uppercase; letter-spacing: -0.2px;
  }
  .item-desc {
    font-family: "Oswald", sans-serif; font-weight: 300;
    font-size: 9.4px; line-height: 12px; color: var(--body-text);
    text-transform: uppercase; letter-spacing: -0.1px;
  }
  .item-price {
    font-family: "Montserrat", sans-serif; font-weight: 700;
    font-size: 5.8px; line-height: 8px; color: var(--gold);
    letter-spacing: 0.6px; text-transform: uppercase;
  }

  .section-divider { position: absolute; left: 120px; top: 424px; width: 540px; height: 16px; }
</style>
</head>
<body>
<main class="menu-page">
  <div class="hero-photo" role="img" aria-label="Close-up photo of a plated steak with a golden fried side and a dish of dipping sauce"></div>

  <section class="menu-panel">
    <h2 class="section-title entrees">ENTREES</h2>

    <div class="item-column col-left entrees-list">
      <article><h3 class="item-name">Chicken Strip Basket</h3><p class="item-desc">Our classic chicken tenders served with your choice of side and dipping sauce.</p><p class="item-price">Small 5.99 / Large 8.99</p></article>
      <article><h3 class="item-name">Grilled Chicken Breast Fillet</h3><p class="item-desc">A classic boneless, skinless chicken breast brushed with a bourbon peppercorn glaze.</p><p class="item-price">Small 7.99 / Large 10.99</p></article>
      <article><h3 class="item-name">Blackened Tilapia</h3><p class="item-desc">8 oz. grilled tilapia filt, blackened and served with your choice of side.</p><p class="item-price">10.99</p></article>
      <article><h3 class="item-name">Deep Fried Catfish</h3><p class="item-desc">Breaded and fried filets, served with tartar sauce.</p><p class="item-price">Small 7.99 / Large 10.99</p></article>
      <article><h3 class="item-name">Pepper Jack Burger Steak</h3><p class="item-desc">A 12oz. ground beef patty smothered in melted pepper jack cheese and jalapeño peppers.</p><p class="item-price">Small 7.99 / Large 10.99</p></article>
      <article><h3 class="item-name">St. Louie Ribs</h3><p class="item-desc">A three pound slab of slow roasted barbecue glazed ribs.</p><p class="item-price">Half rack 13.99 / Full rack 17.99</p></article>
      <article><h3 class="item-name">Pork Stuffed Baked Potato</h3><p class="item-desc">Buttered and salted baked potato stuffed with a mountain of BBQ pulled pork, cheddar and jack cheese, blooming onion petals, sour cream and green onions. Served with a side salad</p><p class="item-price">8.99</p></article>
    </div>

    <div class="item-column col-right entrees-list">
      <article><h3 class="item-name">Harrow Loaded Chicken</h3><p class="item-desc">Our grilled chicken breast piled high with melted jack and cheddar cheese, sautéed onions and mushrooms, crisp bacon, and honey mustard.</p><p class="item-price">Small 9.99 / Large 12.99</p></article>
      <article><h3 class="item-name">Chicken Fried Chicken Dinner</h3><p class="item-desc">Crispy chicken breast smothered in country gravy served with your choice of side and steamed vegetables.</p><p class="item-price">9.99</p></article>
      <article><h3 class="item-name">Fried Shrimp</h3><p class="item-desc">A plate full of lightly breaded butterflied shrimp served with cocktail sauce.</p><p class="item-price">Small 7.99 / Large 10.99</p></article>
      <article><h3 class="item-name">Country Fried Steak</h3><p class="item-desc">Hand breaded and deep fried, smothered in old fashioned country gravy.</p><p class="item-price">Small 7.99 / Large 10.99</p></article>
      <article><h3 class="item-name">Black N' Blue Sirloin</h3><p class="item-desc">12 oz. choice cut sirloin cooked to your request, blackened and topped with melted blue cheese crumbles.</p><p class="item-price">15.99</p></article>
      <article><h3 class="item-name">Iron Griddle Steak</h3><p class="item-desc">12 oz. aged and cut from the strip loin. Cooked to your request.</p><p class="item-price">14.99</p></article>
      <article><h3 class="item-name">Flat Iron Steak</h3><p class="item-desc">9 oz. flat iron seasoned and cooked to your request.</p><p class="item-price">16.99</p></article>
    </div>

    <svg class="section-divider" viewBox="0 0 540 16" aria-hidden="true">
      <defs>
        <linearGradient id="rule" x1="0" x2="1">
          <stop offset="0" stop-color="#c79a4c" stop-opacity="0"/>
          <stop offset="0.5" stop-color="#e2c07a"/>
          <stop offset="1" stop-color="#c79a4c" stop-opacity="0"/>
        </linearGradient>
      </defs>
      <rect x="0" y="7.5" width="540" height="1" fill="url(#rule)"/>
      <circle cx="270" cy="8" r="5" fill="none" stroke="#e2c07a" stroke-width="1.5"/>
    </svg>

    <h2 class="section-title sandwiches">SANDWICHES</h2>

    <div class="item-column col-left sandwiches-list">
      <article><h3 class="item-name">Harrow Club Sandwich</h3><p class="item-desc">Layers of ham, turkey, roast beef, bacon and cheese. Served with mayo on a toasted focaccia bun</p><p class="item-price">9.99</p></article>
      <article><h3 class="item-name">Chicken Breast Sandwich</h3><p class="item-desc">Choice of crispy or grilled chicken breast, lettuce, tomato and pickles. Served with mayo on a toasted bun.</p><p class="item-price">7.99</p></article>
      <article><h3 class="item-name">Bang Bang Turkey Wrap</h3><p class="item-desc">A grilled 12 inch tortilla stuffed with roasted turkey breast, mozzarella cheese, lettuce and our spicy bang bang sauce.</p><p class="item-price">7.99</p></article>
      <article><h3 class="item-name">Roast Beef &amp; Cheddar</h3><p class="item-desc">Thinly sliced slow cooked roast beef smothered with a cheddar cheese sauces on a ciabatta bun. Served with spicy BBQ sauce.</p><p class="item-price">7.99</p></article>
      <article><h3 class="item-name">B.L.T.</h3><p class="item-desc">This classic bacon, lettuce and tomato sandwich is served with mayo on your choice of white, wheat or sourdough toast.</p><p class="item-price">6.99</p></article>
      <article><h3 class="item-name">Ember's Spicy Buffalo Chicken Sandwich</h3><p class="item-desc">Crispy fired chicken breast smothered in Ember's spicy buffalo sauce. Served on a ciabatta bun. Dressed with jalapeño ranch, lettuce, tomato and pickle.</p><p class="item-price">8.99</p></article>
      <article><h3 class="item-name">Triple Decker Reuben</h3><p class="item-desc">Layer after layer of grilled corned beef, sauerkraut, swiss cheese and thousand island dressing. Served on toasted rye.</p><p class="item-price">7.99</p></article>
    </div>

    <div class="item-column col-right sandwiches-list">
      <article><h3 class="item-name">Classic French Dip</h3><p class="item-desc">Thinly sliced roast beef grilled and loaded with swiss cheese and grilled onions. Served with french onion soup.</p><p class="item-price">8.99</p></article>
      <article><h3 class="item-name">Crispy Chicken Bacon Ranch Wrap</h3><p class="item-desc">A 12 inch grilled tortilla stuffed with crispy chicken tenders, bacon, lettuce, tomatoes and ranch dressing.</p><p class="item-price">8.99</p></article>
      <article><h3 class="item-name">Southern Style Pulled Pork</h3><p class="item-desc">Smoked pulled pork smothered in tangy barbecue sauce on a toasted hoagie. Served with cole slaw on request.</p><p class="item-price">7.99</p></article>
      <article><h3 class="item-name">Chicken Fry Steak Sandwich</h3><p class="item-desc">Hand breaded chicken fried steak topped with bacon, lettuce, pickles, tomato and onion.</p><p class="item-price">7.99</p></article>
      <article><h3 class="item-name">Philly Steak &amp; Cheese Sandwich</h3><p class="item-desc">Thinly sliced steak piled high with melted monterey jack cheese, grilled onions and peppers on a toasted hoagie.</p><p class="item-price">7.99</p></article>
      <article><h3 class="item-name">Eight Cheese Grilled Cheese</h3><p class="item-desc">Taking this classic to the gourmet level! Eight cheeses melted thick on toasted sourdough bread.</p><p class="item-price">7.99</p></article>
      <article><h3 class="item-name">Chicken Cordon Bleu Sandwich</h3><p class="item-desc">Your choice of crispy or grilled chicken breast layered with grilled ham, swiss cheese, lettuce, tomatoes and pickles. Served with mayo on a toasted bun.</p><p class="item-price">8.99</p></article>
    </div>
  </section>
</main>
</body>
</html>
```